Hybrid Seed corn and Soybean Sales business needs a website.

We here at "KW Grain" feel that we need a website to show a very professional side to our customer base. Although no actual ordering will take place on this website, we would like to put Plot and field trail data on the website. Along with a brief page for each of our hybrids and a place for customers to sign up for a newsletter. The company we sell hybrids for is MolvanGrain.com... Im not sure how this process works as far as myself updating the information or having the data actually put on the website, but feel free to contact me if you need the information. I will attach the logo for the company, (KW Grain).

Target Market(s)

Farmers, "Producers", Corn and soybean production

Industry/Entity Type

Business

Coding

Coded - Design and coding required

Number of Pages Required

5+ page

Colors
f78f20
ffffff

Requirements
Nice to have
• Similar layout to http://www.molvangrain.com/
• And it would be nice to incorporate our story into the website
• http://www.molvangrain.com/our-story/molvan-today/

```html
<!DOCTYPE html>
<html lang="en">
<head>
<meta charset="utf-8">
<title>KW Grain – Hybrid Seeds of Corn &amp; Soybean</title>
<link href="https://fonts.googleapis.com/css2?family=Montserrat:wght@400;500;600&family=Roboto:wght@300;400;500&display=swap" rel="stylesheet">
<style>
:root{
  --orange:#f07c1e;
  --orange-dark:#d9600f;
  --orange-deep:#b8540e;
  --ink:#1b1b1b;
  --text:#555;
  --muted:#8a8a8a;
  --beige:#efe7df;
  --footer:#111;
  --social:#8a8a8a;
  --white:#fff;
}
*{margin:0;padding:0;box-sizing:border-box}
html,body{width:746px;height:1200px;overflow:hidden;background:var(--white)}
body{position:relative;font-family:'Roboto',sans-serif;color:var(--text)}
.abs{position:absolute}

.site-header{left:0;top:0;width:746px;height:78px;background:linear-gradient(#fbfbfb,#e9e9e9)}
.brand{left:70px;top:30px;display:flex;align-items:center;gap:7px;font-family:'Montserrat',sans-serif;font-weight:600;font-size:19px;color:var(--orange);letter-spacing:1px}
.brand-dot{width:15px;height:15px;border-radius:50%;background:#4f9a2c}
.contact{right:69px;top:49px;font-size:8px;color:#333;display:flex;gap:12px}
.contact span{display:flex;align-items:center;gap:3px}

.main-nav{left:0;top:78px;width:746px;height:37px;background:linear-gradient(var(--orange),var(--orange-dark));border-bottom:1px solid var(--orange-deep)}
.main-nav ul{list-style:none;position:absolute;left:70px;top:0;display:flex;height:37px}
.main-nav li{height:37px;display:flex;align-items:center;justify-content:center;color:var(--white);font-size:7.5px;font-weight:500;border-right:1px solid rgba(0,0,0,.12)}
.main-nav li.active{background:var(--orange-deep)}
.search{left:573px;top:5px;width:104px;height:26px;background:rgba(0,0,0,.12);border:1px solid rgba(0,0,0,.15);color:#f3d2b5;font-size:7.5px;padding:8px}
.search svg{position:absolute;right:8px;top:9px}

.hero{left:0;top:115px;width:746px;height:358px;background:radial-gradient(circle at 50% 45%,#f2a41a 0,#e88a1c 35%,#d8781c 70%,#c9691a 100%)}
.caption{left:0;top:300px;width:746px;height:58px;background:rgba(40,30,25,.62)}
.caption h2{position:absolute;left:70px;top:18px;font-family:'Roboto',sans-serif;font-weight:300;font-size:17px;color:var(--white)}
.dots{right:74px;top:25px;display:flex;gap:4px}
.dots i{width:7px;height:7px;border-radius:50%;background:rgba(255,255,255,.4)}
.dots i.on{background:var(--white)}

.welcome{left:0;top:500px;width:746px;text-align:center}
.welcome h1{font-family:'Montserrat',sans-serif;font-weight:500;font-size:16px;color:var(--ink);letter-spacing:.3px}
.rule{width:48px;height:1px;background:var(--orange);margin:8px auto 0}
.welcome p{width:610px;margin:10px auto 0;font-size:7.4px;line-height:16px}

.card{top:604px;width:192px;height:178px;background:linear-gradient(var(--orange),var(--orange-dark));text-align:center;color:#ffd9b8;border-radius:2px}
.card .icon{width:60px;height:60px;border-radius:50%;background:radial-gradient(#fff 60%,#e8e8e8);margin:20px auto 0;display:flex;align-items:center;justify-content:center}
.card h3{font-family:'Montserrat',sans-serif;font-weight:500;font-size:9.6px;color:var(--white);margin-top:13px}
.card p{font-size:7.2px;line-height:16px;margin:7px 14px 0}

.about{left:70px;top:808px;width:418px}
.about h2{font-family:'Montserrat',sans-serif;font-weight:500;font-size:16px;color:var(--ink)}
.about .rule{margin:6px 0 0}
.about p{font-size:7.4px;line-height:16px;margin-top:5px}
.video{left:506px;top:815px;width:171px;height:96px;background:linear-gradient(#3b2a1c,#8a4a16 55%,#f0a030 78%,#3a2410)}
.play{left:71px;top:34px}

.partners{left:0;top:945px;width:746px;height:72px;background:var(--beige)}
.partner{top:26px;font-family:'Roboto',sans-serif;font-weight:500;font-size:19px;display:flex;align-items:center;gap:6px}

.site-footer{left:0;top:1017px;width:746px;height:140px;background:var(--footer);color:#9a9a9a}
.col{top:20px}
.col h4{font-family:'Montserrat',sans-serif;font-weight:500;font-size:9.5px;color:var(--white);margin-bottom:9px}
.news-item{display:flex;gap:6px;margin-bottom:15px}
.thumb{width:47px;height:31px}
.news-item b{display:block;font-weight:400;font-size:7.5px;color:var(--white);margin-bottom:3px}
.news-item span{font-size:6.5px;line-height:10px;display:block;width:72px}
.links{display:grid;grid-template-columns:70px 80px;row-gap:9px;font-size:6.8px}
.social{list-style:none;font-size:6.8px}
.social li{display:flex;align-items:center;gap:5px;height:16px}
.social i{width:8px;height:8px;background:var(--social)}
.field{width:140px;height:23px;background:#f1ece6;border-radius:2px;font-size:7px;color:#777;padding:8px 7px;margin-bottom:6px}
.btn{width:140px;height:23px;background:linear-gradient(var(--orange),var(--orange-dark));border-radius:2px;font-size:7px;font-weight:500;color:var(--white);text-align:center;line-height:23px}
.copyright{left:0;top:1174px;width:746px;text-align:center;font-size:7px;color:#555}
</style>
</head>
<body>

<header class="site-header abs">
  <div class="brand abs"><span class="brand-dot"></span>KW GRAIN</div>
  <div class="contact abs">
    <span><svg width="7" height="7" viewBox="0 0 10 10"><path d="M2 0l2 2-1 2 3 3 2-1 2 2-2 2C4 10 0 6 0 2z" fill="#f07c1e"/></svg>555 210 4480</span>
    <span><svg width="8" height="6" viewBox="0 0 10 7"><rect width="10" height="7" fill="#f07c1e"/><path d="M0 0l5 4 5-4" stroke="#fff" fill="none"/></svg>hello@kwgrain.example</span>
  </div>
</header>

<nav class="main-nav abs">
  <ul>
    <li class="active" style="width:64px">HOME</li>
    <li style="width:75px">ABOUT US</li>
    <li style="width:77px">PRODUCTS</li>
    <li style="width:75px">SERVICES</li>
    <li style="width:59px">NEWS</li>
    <li style="width:64px">BLOG</li>
    <li style="width:81px">CONTACT US</li>
  </ul>
  <div class="search abs">Search...
    <svg width="8" height="8" viewBox="0 0 10 10"><circle cx="4" cy="4" r="3" stroke="#f3d2b5" fill="none" stroke-width="1.5"/><path d="M6.5 6.5L9.5 9.5" stroke="#f3d2b5" stroke-width="1.5"/></svg>
  </div>
</nav>

<section class="hero abs" role="img" aria-label="Magnifying glass held over golden corn kernels">
  <div class="caption abs">
    <h2>We sell hybrid seeds of Corn &amp; Soybean</h2>
    <div class="dots abs"><i></i><i class="on"></i><i></i><i></i></div>
  </div>
</section>

<section class="welcome abs">
  <h1>WELCOME TO KW GRAIN</h1>
  <div class="rule"></div>
  <p>Lorem ipsum dolor sit amet, consectetuer adipiscing elit, sed diam nonummy nibh euismod tincidunt ut laoreet dolore magna aliquam erat volutpat. Ut wisi enim ad minim veniam, quis nostrud exerci tation ullamcorper suscipit lobortis nisl ut aliquip ex ea commodo consequat. Duis autem vel eum iriure dolor in hendrerit in vulputate velit esse molestie con sequat, vel illum dolore eu feugiat nulla facilisis at vero eros et accumsan et iusto odio dignissim.</p>
</section>

<article class="card abs" style="left:70px">
  <div class="icon"><svg width="26" height="30" viewBox="0 0 26 30"><ellipse cx="13" cy="13" rx="6" ry="11" fill="#f07c1e"/><path d="M2 20c5 0 9 3 11 9 2-6 6-9 11-9-4 4-7 7-11 7S6 24 2 20z" fill="#d9600f"/></svg></div>
  <h3>LOREM IPSUM DOLOR</h3>
  <p>Ut wisi enim ad minim veniam, quis nostrud exerci tation ullamcorper suscipit lobortis nisl ut aliquip ex ea commodo consequat.</p>
</article>
<article class="card abs" style="left:277px">
  <div class="icon"><svg width="28" height="26" viewBox="0 0 28 26"><path d="M3 23C5 12 14 3 25 3 23 14 14 23 3 23z" fill="#f07c1e"/><circle cx="11" cy="16" r="2.2" fill="#fff"/><circle cx="15" cy="12" r="2.2" fill="#fff"/><circle cx="19" cy="8" r="2.2" fill="#fff"/></svg></div>
  <h3>DUIS AUTEM VEL EUM IRIURE</h3>
  <p>Lorem ipsum dolor sit amet, consectetuer adipiscing elit, sed diam nonummy nibh eui smod tincidunt ut laoreet dolore.</p>
</article>
<article class="card abs" style="left:485px">
  <div class="icon"><svg width="28" height="26" viewBox="0 0 28 26"><g fill="#f07c1e"><circle cx="18" cy="3" r="1.6"/><circle cx="16" cy="7" r="1.6"/><circle cx="20" cy="7" r="1.6"/><circle cx="14" cy="11" r="1.6"/><circle cx="18" cy="11" r="1.6"/><circle cx="22" cy="11" r="1.6"/><circle cx="16" cy="15" r="1.6"/><circle cx="20" cy="15" r="1.6"/><circle cx="24" cy="15" r="1.6"/><path d="M1 16h8l6 4h10v3H13L8 21H1z"/></g></svg></div>
  <h3>EODEM MODO TYPI</h3>
  <p>Ut wisi enim ad minim veniam, quis nostrud exerci tation ullamcorper suscipit lobortis nisl ut aliquip ex ea commodo consequat.</p>
</article>

<section class="about abs">
  <h2>ABOUT US</h2>
  <div class="rule"></div>
  <p>Lorem ipsum dolor sit amet, consectetuer adipiscing elit, sed diam nonummy nibh euismod tincidunt ut laoreet dolore magna aliquam erat volutpat. Ut wisi enim ad minim veniam, quis nostrud exerci tation ullamcorper suscipit lobortis nisl ut aliquip ex ea commodo consequat.<br>Duis autem vel eum iriure dolor in hendrerit in vulputate velit esse molestie con sequat, vel illum dolore eu feugiat nulla faci lisis at vero eros et accumsan et iusto odio dignissim.</p>
</section>
<div class="video abs" role="img" aria-label="Video thumbnail of a sunset over a cornfield">
  <svg class="play abs" width="28" height="28" viewBox="0 0 28 28"><circle cx="14" cy="14" r="12" stroke="#fff" stroke-width="2" fill="rgba(0,0,0,.2)"/><path d="M11 8l9 6-9 6z" fill="#fff"/></svg>
</div>

<section class="partners abs">
  <div class="partner abs" style="left:190px;color:#222"><i style="width:12px;height:12px;background:#f07c1e;display:block"></i>Molvan</div>
  <div class="partner abs" style="left:323px;color:#176a8a"><i style="width:12px;height:12px;border-radius:50%;background:#3aa040;display:block"></i>Verdant</div>
  <div class="partner abs" style="left:465px;top:30px;font-size:9px;color:#222"><i style="width:10px;height:10px;background:#d0202a;display:block"></i>Corvel AgriScience</div>
</section>

<footer class="site-footer abs">
  <div class="col abs" style="left:70px">
    <h4>LATEST NEWS</h4>
    <div class="news-item"><div class="thumb" role="img" aria-label="Ear of corn in a field" style="background:linear-gradient(90deg,#7a5a30,#d8a050,#6a7a3a)"></div><div><b>Lorem ipsum dolor sit</b><span>Ut wisi enim ad minim veniam, quis nostrud...</span></div></div>
    <div class="news-item"><div class="thumb" role="img" aria-label="Young green corn field" style="background:linear-gradient(#9cc8e8,#5a9a30 45%,#3a7a20)"></div><div><b>Lorem ipsum dolor sit</b><span>Ut wisi enim ad minim veniam, quis nostrud...</span></div></div>
  </div>
  <div class="col abs" style="left:248px">
    <h4>QUICK LINKS</h4>
    <div class="links"><span>Home</span><span>Products</span><span>About Us</span><span>Privacy Policy</span><span>Our Service</span><span>Sitemap</span><span>FAQ</span><span>Terms &amp; Conditions</span><span>Contact Us</span></div>
  </div>
  <div class="col abs" style="left:430px">
    <h4>CONNECT US</h4>
    <ul class="social">
      <li><i></i>Fieldpost</li>
      <li><i></i>Chatterly</li>
      <li><i></i>Worklink</li>
      <li><i></i>Circlenet</li>
      <li><i style="background:var(--orange)"></i>RSS</li>
    </ul>
  </div>
  <div class="col abs" style="left:537px">
    <h4>NEWSLETTER SIGNUP</h4>
    <div class="field">Name</div>
    <div class="field">Email Address</div>
    <div class="btn">SUBSCRIBE</div>
  </div>
</footer>

<p class="copyright abs">Copyrights @ 2015 KW Grain. All Right Reserved.</p>

</body>
</html>
```